QVR business card

Need a business card for a company that provides instructional design and elearning development services. The website is here: http://quorvane.studio/

I'm attaching a current logo, as well as the old business card design. While I like to keep it clean, the old design is too simplistic for my liking. The only idea I want to reuse from the old design is placing industry jargon on the back of the card, just need a better way to present it. But if you have other ideas for the back--feel free to experiment.

Please use the colors complementary to the color we have on the website. Thank you!

```html
<!DOCTYPE html>
<html lang="en">
<head>
<meta charset="utf-8">
<title>QVR business card</title>
<link rel="stylesheet" href="https://fonts.googleapis.com/css2?family=Oswald:wght@300;400&family=Source+Sans+3:wght@400;600&display=swap">
<style>
  :root {
    --backdrop: #ece7df;
    --card: #ffffff;
    --card-edge: #6f6657;
    --teal: #13aeaa;
    --gold: #d9c98d;
    --ink: #2b2b2b;
    --ink-soft: #3d3d3d;
    --rule: #b9b9b9;
  }
  * { margin: 0; padding: 0; box-sizing: border-box; }
  html, body {
    width: 1200px; height: 1177px; overflow: hidden;
    background: var(--backdrop);
  }
  .canvas { position: relative; width: 1200px; height: 1177px; }

  .card {
    position: absolute;
    background: var(--card);
    border: 1.5px solid var(--card-edge);
    border-radius: 34px;
    overflow: hidden;
  }

  /* Front */
  .card--front { left: 60px; top: 46px; width: 875px; height: 499px; }
  .card__accent {
    position: absolute; left: 0; top: 67px; width: 15px; height: 56px;
    background: var(--teal);
  }
  .holder { position: absolute; left: 28px; top: 56px; font-family: "Source Sans 3", sans-serif; }
  .holder__name { font-size: 27px; font-weight: 600; color: var(--teal); line-height: 1.25; }
  .holder__role { font-size: 26px; font-weight: 400; color: var(--ink-soft); line-height: 1.25; }

  .brand {
    position: absolute; left: 420px; top: 40px;
    display: flex; align-items: center; gap: 22px;
  }
  .brand__mark { width: 54px; height: 54px; background: var(--teal); }
  .brand__name {
    font-family: "Source Sans 3", sans-serif; font-weight: 600;
    font-size: 100px; line-height: 1; color: var(--gold); letter-spacing: 4px;
  }

  .contact {
    position: absolute; left: 26px; top: 308px; list-style: none;
    font-family: "Source Sans 3", sans-serif; font-size: 21px; color: var(--ink);
  }
  .contact__item { display: flex; align-items: center; gap: 10px; height: 38px; }
  .contact__icon { width: 18px; height: 18px; }

  .card__band { position: absolute; left: 0; bottom: 0; width: 875px; height: 68px; }
  .website {
    position: absolute; right: 28px; bottom: 14px;
    font-family: "Source Sans 3", sans-serif; font-size: 21px;
    letter-spacing: 2.5px; color: var(--ink);
  }

  /* Back */
  .card--back { left: 257px; top: 601px; width: 880px; height: 498px; }
  .pitch {
    position: absolute; left: 20px; top: 18px; width: 270px;
    font-family: "Oswald", sans-serif; font-weight: 400;
    font-size: 100px; line-height: 121px; text-align: center;
    color: var(--ink); text-transform: uppercase;
  }
  .divider {
    position: absolute; left: 325px; top: 38px; width: 2px; height: 432px;
    background: var(--rule);
  }
  .jargon {
    position: absolute; left: 379px; top: 24px; list-style: none;
    font-family: "Oswald", sans-serif; font-weight: 400;
    font-size: 38px; line-height: 76px; letter-spacing: 1.5px;
    color: var(--ink); text-transform: uppercase;
  }
</style>
</head>
<body>
<main class="canvas">

  <section class="card card--front" aria-label="Card front">
    <span class="card__accent"></span>
    <div class="holder">
      <p class="holder__name">Marta Velinskaya</p>
      <p class="holder__role">Managing Director</p>
    </div>

    <div class="brand">
      <span class="brand__mark"></span>
      <span class="brand__name">QVR</span>
    </div>

    <ul class="contact">
      <li class="contact__item">
        <svg class="contact__icon" viewBox="0 0 18 18" aria-hidden="true">
          <circle cx="9" cy="9" r="8" fill="none" stroke="var(--teal)" stroke-width="1.4"/>
          <path d="M6 4.5l1.8 2.2-1 1.2a6 6 0 0 0 3.3 3.3l1.2-1 2.2 1.8-1 1.5c-3.8-.2-7.3-3.7-7.5-7.5z" fill="var(--teal)"/>
        </svg>
        <span>555-204-7731</span>
      </li>
      <li class="contact__item">
        <svg class="contact__icon" viewBox="0 0 18 18" aria-hidden="true">
          <rect x="1" y="4" width="16" height="11" rx="1.5" fill="var(--teal)"/>
          <path d="M1.8 5l7.2 5.5L16.2 5" fill="none" stroke="#fff" stroke-width="1.5"/>
        </svg>
        <span>mvelinskaya@quorvane.studio</span>
      </li>
    </ul>

    <svg class="card__band" viewBox="0 0 875 68" preserveAspectRatio="none" aria-hidden="true">
      <rect x="0" y="0" width="875" height="36" fill="var(--teal)"/>
      <rect x="0" y="36" width="875" height="32" fill="var(--gold)"/>
      <path d="M875 0H560C535 0 530 8 520 20C512 30 505 36 490 36H875Z" fill="var(--gold)"/>
    </svg>
    <p class="website">www.quorvane.studio</p>
  </section>

  <section class="card card--back" aria-label="Card back">
    <h2 class="pitch">How<br>can<br>we<br>help?</h2>
    <span class="divider"></span>
    <ul class="jargon">
      <li>Mobile Learning SCORM</li>
      <li>Instructional Design LMS</li>
      <li>MOOCs eLearning HTML5</li>
      <li>Adult Learning Theory</li>
      <li>Gamification Classroom</li>
      <li>xAPI Blended Learning</li>
    </ul>
  </section>

</main>
</body>
</html>
```